RW Holloway LLC Business Card - Civil Engineering & Consulting Firm

We need a Business Card that is elegant, and masculine.  It is our Professional Civil Engineering & Consulting Company located in San Antonio TX (Not s construction or builder firm- no gears & no tool images please). We provide civil engineering services including  commercial site plans, grading and drainage plans, utility plans, hydraulics and hydrology, land planning, utility coordination, and other general civil engineering services related to commercial and residential development.
We have 2 existing Logos. We would like to convey reliability, strength, trustworthiness and attention to detail.  Blues and orange tones as per logo We are OK with the use of a darker blue in the mix.  We have 2 logo versions - Full Company Name Logo to go on the back of card, & Small Icon Logo for the front w/ personal Info.

Target Market(s)
Architects, Real Estate Developers, Other Strctural Engineers, Surveyers, General Contractors
Industry/Entity Type
Professional Civil Engineering
Contact Information for Business Card
Name, Position, Address, Cell & Office #, email, and company website
Font styles to use
Other font styles liked:
- Avian
Requirements
Should not have
- No Tools, No Gears, no Cranes, or Construction Equipment.

```html
<!DOCTYPE html>
<html lang="en">
<head>
<meta charset="utf-8">
<title>RW Holloway LLC – Business Card</title>
<link rel="stylesheet" href="https://fonts.googleapis.com/css2?family=Josefin+Sans:wght@300;400&family=Arimo:wght@400&display=swap">
<style>
  :root {
    --backdrop: #2c2c2e;
    --sky-blue: #7aaed8;
    --brand-blue: #6fa3d6;
    --brand-orange: #ee8a26;
    --brand-yellow: #fbbf16;
    --paper: #ffffff;
    --ink: #111111;
  }
  * { box-sizing: border-box; margin: 0; padding: 0; }
  html, body {
    width: 1200px; height: 1015px; overflow: hidden;
    background: var(--backdrop);
  }
  .canvas {
    position: relative; width: 1200px; height: 1015px;
    display: flex; flex-direction: column; align-items: center;
    justify-content: center; gap: 40px;
  }
  .card {
    position: relative; width: 800px; height: 457px;
    box-shadow: 0 10px 30px rgba(0,0,0,.5);
    overflow: hidden;
  }
  /* Back of card */
  .card-back {
    background: var(--sky-blue);
    display: flex; align-items: center; justify-content: center;
  }
  .card-back .company-name {
    font-family: "Josefin Sans", sans-serif; font-weight: 300;
    font-size: 60px; letter-spacing: 6px; text-transform: uppercase;
    color: var(--paper);
  }
  /* Front of card */
  .card-front { background: var(--paper); }
  .card-front .company-name {
    position: absolute; left: 70px; top: 70px;
    font-family: "Josefin Sans", sans-serif; font-weight: 300;
    font-size: 40px; letter-spacing: 3px; text-transform: uppercase;
    color: var(--brand-blue);
  }
  .accent-square {
    position: absolute; left: 0; top: 258px;
    width: 58px; height: 58px; background: var(--brand-blue);
  }
  .bar-composition {
    position: absolute; right: 0; top: 0;
    width: 300px; height: 457px;
  }
  .bar-composition .bar-blue { fill: var(--brand-blue); }
  .bar-composition .bar-orange { fill: var(--brand-orange); }
  .bar-composition .bar-yellow { fill: var(--brand-yellow); }
  .contact {
    position: absolute; left: 90px; top: 190px;
    font-family: Arimo, Arial, sans-serif; color: var(--ink);
  }
  .person-name {
    font-family: "Josefin Sans", sans-serif; font-weight: 400;
    font-size: 34px; text-transform: uppercase; line-height: 1;
    color: var(--brand-blue);
  }
  .person-name .surname { color: var(--brand-orange); }
  .person-title { font-size: 22px; margin-top: 4px; }
  .contact-list { list-style: none; margin-top: 18px; }
  .contact-list li {
    display: flex; align-items: center; gap: 10px;
    font-size: 21px; line-height: 28px;
  }
  .contact-list svg { width: 18px; height: 18px; flex: none; fill: var(--brand-blue); }
  .contact-list .highlight { color: var(--brand-orange); }
  .address { margin-top: 20px; font-size: 21px; line-height: 25px; font-style: normal; }
</style>
</head>
<body>
<main class="canvas">
  <section class="card card-back" aria-label="Card back">
    <p class="company-name">RW Holloway LLC</p>
  </section>

  <section class="card card-front" aria-label="Card front">
    <p class="company-name">RW Holloway LLC</p>
    <div class="accent-square"></div>

    <svg class="bar-composition" viewBox="0 0 300 457" aria-hidden="true">
      <rect class="bar-blue" x="20" y="0" width="22" height="60"/>
      <rect class="bar-blue" x="20" y="90" width="22" height="367"/>
      <rect class="bar-blue" x="80" y="40" width="22" height="417"/>
      <rect class="bar-orange" x="140" y="0" width="24" height="457"/>
      <rect class="bar-orange" x="200" y="70" width="24" height="160"/>
      <rect class="bar-yellow" x="200" y="280" width="24" height="177"/>
      <rect class="bar-yellow" x="255" y="330" width="24" height="127"/>
    </svg>

    <div class="contact">
      <h1 class="person-name">Daniel <span class="surname">Reyes</span></h1>
      <p class="person-title">Managing Director</p>
      <ul class="contact-list">
        <li>
          <svg viewBox="0 0 24 24" aria-hidden="true"><path d="M6.6 10.8a15 15 0 0 0 6.6 6.6l2.2-2.2a1 1 0 0 1 1-.25 11.4 11.4 0 0 0 3.6.57 1 1 0 0 1 1 1V20a1 1 0 0 1-1 1A17 17 0 0 1 3 4a1 1 0 0 1 1-1h3.5a1 1 0 0 1 1 1c0 1.250.2 2.450.57 3.57a1 1 0 0 1-.25 1z"/></svg>
          044-555 210 384
        </li>
        <li>
          <svg viewBox="0 0 24 24" aria-hidden="true"><path d="M2 5h20v14H2zm2 2v.4l8 5 8-5V7l-8 5z"/></svg>
          info@hollowayce.com
        </li>
        <li>
          <svg viewBox="0 0 24 24" aria-hidden="true"><path d="M12 2a10 10 0 1 0 0 20 10 10 0 0 0 0-20zm0 2c1 1.3 1.8 3 2.2 5H9.8c.4-2 1.2-3.7 2.2-5zM4.3 14a8 8 0 0 1 0-4h3.4a16 16 0 0 0 0 4zm5.5 0a14 14 0 0 1 0-4h4.4a14 14 0 0 1 0 4zm6.5 0a16 16 0 0 0 0-4h3.4a8 8 0 0 1 0 4zM12 20c-1-1.3-1.8-3-2.2-5h4.4c-.4 2-1.2 3.7-2.2 5z"/></svg>
          <span>www.<span class="highlight">hollowayce</span>.com</span>
        </li>
      </ul>
      <address class="address">421, Address line goes here<br>45452, Country Name</address>
    </div>
  </section>
</main>
</body>
</html>
```